Local Flower Farm Needs Business Card Design

I need business cards designed for a flower farm based in Eudora, Kansas.
Business Info:
We are a local cut flower farm located in Eudora, Kansas, founded by Corinne Haldwick. What started as a passion for agriculture and search for more joy in daily life has blossomed into a small business dedicated to providing the community with beautiful, fresh, and sustainable flowers. We specialize in local, seasonal blooms, ensuring that every petal reflects the care and dedication we pour into our craft. Our mission is to deliver the highest quality flowers directly to our customers through local farmers markets and to florists who share our commitment to sustainability. Join us in celebrating the beauty of nature, one bloom at a time!
Contact Details:
Corinne Haldwick
Owner
Phone 913-555-0147
Facebook: Rosalind Thorpe Gardens
Instagram: @RosalindThorpeGardens
Website: RosalindThorpeGardens.example
Target Market(s)
Wholesale to Florists and Direct to Consumer via Farmers Market
Industry/Entity Type
Florist, Farm
Contact Information for Business Card
Name, Contact Info, Logo
Look and feel
Each slider illustrates characteristics of the customer's brand and the style your logo design should communicate.

```html
<!DOCTYPE html>
<html lang="en">
<head>
<meta charset="utf-8">
<title>Rosalind Thorpe Gardens – Business Card</title>
<link href="https://fonts.googleapis.com/css2?family=Arimo:wght@400;700&display=swap" rel="stylesheet">
<style>
  :root {
    --backdrop: #d5d8d8;
    --card: #f7f7f6;
    --ink: #0e1c1c;
    --ink-soft: #3a4444;
    --band-text: #ffffff;
    --muted: #8a9090;
    --faint: #ececea;
  }
  html, body {
    margin: 0;
    padding: 0;
    width: 1200px;
    height: 829px;
    overflow: hidden;
    background: var(--backdrop);
    font-family: "Arimo", Arial, sans-serif;
  }
  .stage {
    position: relative;
    width: 1200px;
    height: 829px;
  }
  .card {
    position: absolute;
    top: 268px;
    width: 520px;
    height: 297px;
    background: var(--card);
    box-shadow: 0 6px 18px rgba(0,0,0,0.12);
    overflow: hidden;
  }
  .card--front { left: 50px; }
  .card--back { left: 630px; }

  .band {
    position: absolute;
    left: 0;
    right: 0;
    top: 48px;
    height: 56px;
    background: var(--ink);
  }
  .holder {
    position: absolute;
    left: 42px;
    top: 56px;
    color: var(--band-text);
  }
  .holder__name {
    font-weight: 700;
    font-size: 22px;
    letter-spacing: 0.5px;
    text-transform: uppercase;
    line-height: 1.1;
  }
  .holder__role {
    font-size: 12px;
    color: #c9d0d0;
    margin-top: 2px;
  }

  .contacts {
    position: absolute;
    left: 34px;
    top: 150px;
    margin: 0;
    padding: 0;
    list-style: none;
    color: var(--ink-soft);
    font-size: 14px;
    line-height: 22px;
  }
  .contacts li {
    display: flex;
    align-items: center;
    gap: 7px;
  }
  .contacts svg { flex: none; }

  .seal {
    position: absolute;
    display: flex;
    align-items: center;
    justify-content: center;
    text-align: center;
    border-radius: 50%;
    background: var(--card);
    border: 1.5px solid var(--ink);
    color: var(--ink);
    font-weight: 700;
    text-transform: uppercase;
    letter-spacing: 1px;
    box-sizing: border-box;
  }
  .card--front .seal {
    width: 132px;
    height: 132px;
    left: 338px;
    top: 96px;
    font-size: 13px;
    line-height: 1.35;
    padding: 14px;
  }
  .card--back .seal {
    width: 150px;
    height: 150px;
    left: 278px;
    top: 74px;
    font-size: 15px;
    line-height: 1.35;
    padding: 16px;
  }

  .floral-wash {
    position: absolute;
    left: 20px;
    top: 0;
    width: 230px;
    height: 297px;
    background: linear-gradient(160deg, var(--faint), rgba(236,236,234,0));
  }
</style>
</head>
<body>
<main class="stage">
  <section class="card card--front" aria-label="Business card front">
    <div class="band"></div>
    <div class="holder">
      <div class="holder__name">Corinne Haldwick</div>
      <div class="holder__role">Owner</div>
    </div>
    <div class="seal">Rosalind Thorpe Gardens</div>
    <ul class="contacts">
      <li>
        <svg width="11" height="11" viewBox="0 0 24 24" aria-hidden="true"><path fill="#0e1c1c" d="M6.6 10.8a15.1 15.1 0 0 0 6.6 6.6l2.2-2.2a1 1 0 0 1 1-.25 11.4 11.4 0 0 0 3.6.57 1 1 0 0 1 1 1V20a1 1 0 0 1-1 1A17 17 0 0 1 3 4a1 1 0 0 1 1-1h3.5a1 1 0 0 1 1 1c0 1.25.2 2.45.57 3.57a1 1 0 0 1-.25 1z"/></svg>
        913-555-0147
      </li>
      <li>
        <svg width="11" height="11" viewBox="0 0 12 12" aria-hidden="true"><circle cx="6" cy="6" r="5.5" fill="#0e1c1c"/></svg>
        Rosalind Thorpe Gardens
      </li>
      <li>
        <svg width="11" height="11" viewBox="0 0 12 12" aria-hidden="true"><circle cx="6" cy="6" r="5.5" fill="#0e1c1c"/></svg>
        @RosalindThorpeGardens
      </li>
      <li>
        <svg width="11" height="11" viewBox="0 0 12 12" aria-hidden="true"><circle cx="6" cy="6" r="5.5" fill="#0e1c1c"/></svg>
        RosalindThorpeGardens.example
      </li>
    </ul>
  </section>

  <section class="card card--back" aria-label="Business card back">
    <div class="floral-wash" role="img" aria-label="Faint botanical line drawing of stems and blossoms"></div>
    <div class="seal">Rosalind Thorpe Gardens</div>
  </section>
</main>
</body>
</html>
```